Building company buisness cards

We are looking for a sharp modern new look for our business cards.We are a New Zealand based company that specialises in house and land packages.We have attached a photo of the current logo and would like to see if it can be improved somehow if needed.We are open to any colours but we have chosen Black and White at this stage. Feel free to change the font and make the logo smarter looking.Play with the colours and see what looks best.We want a card that looks so good know one will want to throw it away!

Target Market(s)

Building profesonals, home buyers

Industry/Entity Type

Building

Contact Information for Business Card

Garrick Tenwood
0275390628
garrickt@hartvale.co.nz

Font styles to use
Serif
Sans Serif

Colors

Designer to choose colors to be used in the design.

Requirements
Must have
• Just the logo on one side and details on the other
• Clean simple looking card
Nice to have
• Round corners and detail like raised or spot UV
• Something that stands out
Should not have
• To title needed, Director etc

```html
<!DOCTYPE html>
<html lang="en">
<head>
<meta charset="utf-8">
<title>Hartvale Business Cards</title>
<link href="https://fonts.googleapis.com/css2?family=Jost:wght@400;500&display=swap" rel="stylesheet">
<style>
  :root {
    --brand-blue: #005a9c;
    --brand-orange: #ef9b22;
    --ink-grey: #555a60;
    --rule-grey: #c9c9c9;
    --card-white: #ffffff;
    --backdrop: #e6e6e6;
  }
  * { margin: 0; padding: 0; box-sizing: border-box; }
  html, body {
    width: 1125px;
    height: 1200px;
    overflow: hidden;
    background: var(--backdrop);
    font-family: "Jost", sans-serif;
  }
  .card {
    position: absolute;
    left: 156px;
    width: 824px;
    height: 470px;
    border-radius: 22px;
    overflow: hidden;
  }
  .card--front { top: 106px; background: var(--card-white); }
  .card--back { top: 639px; background: var(--brand-blue); }

  .front-logo {
    position: absolute;
    left: 60px;
    top: 196px;
    width: 380px;
    height: 76px;
    display: flex;
    align-items: center;
    justify-content: flex-end;
    gap: 14px;
  }
  .front-logo__name {
    color: var(--brand-blue);
    font-size: 50px;
    font-weight: 400;
    line-height: 1;
    white-space: nowrap;
  }
  .front-logo__ring {
    width: 70px;
    height: 70px;
    flex: none;
    border: 4px solid var(--brand-orange);
    border-radius: 50%;
  }
  .divider {
    position: absolute;
    left: 462px;
    top: 152px;
    width: 1px;
    height: 167px;
    background: var(--rule-grey);
  }
  .contact {
    position: absolute;
    left: 500px;
    top: 160px;
  }
  .contact__name {
    color: var(--brand-blue);
    font-size: 30px;
    font-weight: 400;
    line-height: 1;
    margin-bottom: 20px;
  }
  .contact__row {
    display: flex;
    align-items: center;
    gap: 9px;
    color: var(--ink-grey);
    font-size: 20px;
    line-height: 27px;
    white-space: nowrap;
  }
  .contact__icon { width: 19px; height: 19px; flex: none; }

  .accent-band {
    position: absolute;
    left: 0;
    bottom: 0;
    width: 824px;
    height: 16px;
  }

  .back-mark {
    position: absolute;
    left: 50%;
    top: 235px;
    transform: translate(-50%, -50%);
    width: 196px;
    height: 196px;
    border: 5px solid var(--card-white);
    border-radius: 50%;
    display: flex;
    align-items: center;
    justify-content: center;
  }
  .back-mark__name {
    color: var(--card-white);
    font-size: 30px;
    font-weight: 400;
    letter-spacing: 2px;
  }
  .back-web {
    position: absolute;
    left: 0;
    right: 0;
    top: 402px;
    text-align: center;
    color: var(--card-white);
    font-size: 18px;
    letter-spacing: 7.5px;
  }
</style>
</head>
<body>
  <section class="card card--front">
    <div class="front-logo">
      <span class="front-logo__name">HARTVALE</span>
      <span class="front-logo__ring"></span>
    </div>
    <div class="divider"></div>
    <div class="contact">
      <p class="contact__name">Garrick Tenwood</p>
      <p class="contact__row">
        <svg class="contact__icon" viewBox="0 0 20 20" aria-hidden="true">
          <circle cx="10" cy="10" r="8.8" fill="none" stroke="var(--brand-blue)" stroke-width="1.4"/>
          <path d="M7 5.5c-.8.3-1.4 1-1.3 2 .4 3 3.8 6.5 6.8 6.9 1 .1 1.7-.5 2-1.3l-1.9-1.3-1 .9c-1.4-.6-2.8-2-3.4-3.4l.9-1z" fill="var(--brand-blue)"/>
        </svg>
        <span>0275390628</span>
      </p>
      <p class="contact__row">
        <svg class="contact__icon" viewBox="0 0 20 20" aria-hidden="true">
          <circle cx="10" cy="10" r="8.8" fill="none" stroke="var(--brand-blue)" stroke-width="1.4"/>
          <rect x="5.5" y="7" width="9" height="6.5" rx="0.8" fill="var(--brand-blue)"/>
          <path d="M5.8 7.4 10 10.6l4.2-3.2" fill="none" stroke="#fff" stroke-width="0.9"/>
        </svg>
        <span>garrickt@hartvale.co.nz</span>
      </p>
      <p class="contact__row">
        <svg class="contact__icon" viewBox="0 0 20 20" aria-hidden="true">
          <circle cx="10" cy="10" r="8.8" fill="none" stroke="var(--brand-blue)" stroke-width="1.4"/>
          <circle cx="10" cy="10" r="4.6" fill="var(--brand-blue)"/>
          <path d="M5.6 10h8.8M10 5.4c-1.6 2.8-1.6 6.4 0 9.2M10 5.4c1.6 2.8 1.6 6.4 0 9.2" fill="none" stroke="#fff" stroke-width="0.7"/>
        </svg>
        <span>www.hartvale.co.nz</span>
      </p>
    </div>
    <svg class="accent-band" viewBox="0 0 824 16" aria-hidden="true">
      <polygon points="0,0 540,0 534,16 0,16" fill="var(--brand-blue)"/>
      <polygon points="545,0 824,0 824,16 539,16" fill="var(--brand-orange)"/>
    </svg>
  </section>

  <section class="card card--back">
    <div class="back-mark">
      <span class="back-mark__name">HARTVALE</span>
    </div>
    <p class="back-web">www.Hartvale.co.nz</p>
  </section>
</body>
</html>
```